Rollers & Glides.com

Vertical Business Card with focus on branding with our icon. Information on card will be logo, persons name, position, phone number, email address and website. Use the the name Marcus Pellow, position President, phone number 480.915.2267, email Marcus@rollersandglides-demo.com, website www.rollersandglides-demo.com.

```html
<!DOCTYPE html>
<html lang="en">
<head>
<meta charset="utf-8">
<title>Rollers &amp; Glides.com — Business Card</title>
<link rel="stylesheet" href="https://fonts.googleapis.com/css2?family=Arimo:wght@400;700&family=Roboto:wght@400&display=swap">
<style>
  :root {
    --stage: #1c1c1d;
    --card: #0b0b0c;
    --card-edge: #1f1f21;
    --brand-blue: #3a66c4;
    --silver: #c9c9cc;
    --ink: #f2f2f2;
    --divider: #3a3a3d;
  }
  * { margin: 0; padding: 0; box-sizing: border-box; }
  html, body { width: 1200px; height: 900px; overflow: hidden; background: var(--stage); }
  .stage { position: relative; width: 1200px; height: 900px; }

  .card {
    position: absolute;
    width: 540px;
    height: 310px;
    background: var(--card);
    border-radius: 22px;
    box-shadow: 0 0 0 1px var(--card-edge), 0 18px 40px rgba(0,0,0,.55);
  }
  .card--back { left: 610px; top: 120px; }
  .card--front { left: 60px; top: 480px; }

  /* Back side */
  .back-brand {
    position: absolute; inset: 0;
    display: flex; flex-direction: column; align-items: center; justify-content: center; gap: 22px;
  }
  .brand-dot { width: 64px; height: 64px; border-radius: 50%; }
  .back-brand .brand-dot { background: var(--silver); }
  .brand-name {
    font-family: "Roboto", sans-serif; font-weight: 400; letter-spacing: 1.5px;
  }
  .back-brand .brand-name { color: var(--ink); font-size: 30px; }

  /* Front side */
  .front-brand {
    position: absolute; left: 0; top: 0; width: 230px; height: 100%;
    display: flex; flex-direction: column; align-items: center; justify-content: center; gap: 18px;
  }
  .front-brand .brand-dot { background: var(--brand-blue); width: 56px; height: 56px; }
  .front-brand .brand-name { color: var(--brand-blue); font-size: 21px; }

  .divider {
    position: absolute; left: 238px; top: 62px; width: 1px; height: 190px; background: var(--divider);
  }

  .contact {
    position: absolute; left: 262px; top: 78px; right: 20px;
    font-family: "Arimo", sans-serif; color: var(--ink);
  }
  .person-name { font-weight: 700; font-size: 22px; color: var(--brand-blue); letter-spacing: .3px; }
  .person-role { font-size: 17px; margin-top: 2px; }
  .contact-list { list-style: none; margin-top: 22px; display: flex; flex-direction: column; gap: 9px; }
  .contact-item { display: flex; align-items: center; gap: 9px; font-size: 14.5px; white-space: nowrap; }
  .contact-icon { width: 16px; height: 16px; flex: none; }
  .accent { color: var(--brand-blue); }
</style>
</head>
<body>
<main class="stage">

  <section class="card card--back" aria-label="Business card, back">
    <div class="back-brand">
      <span class="brand-dot"></span>
      <span class="brand-name">Rollers &amp; Glides.com</span>
    </div>
  </section>

  <section class="card card--front" aria-label="Business card, front">
    <div class="front-brand">
      <span class="brand-dot"></span>
      <span class="brand-name">Rollers &amp; Glides.com</span>
    </div>

    <div class="divider"></div>

    <div class="contact">
      <p class="person-name">MARCUS PELLOW</p>
      <p class="person-role">President</p>
      <ul class="contact-list">
        <li class="contact-item">
          <svg class="contact-icon" viewBox="0 0 16 16" aria-hidden="true">
            <path d="M4 1.5l2.3 3-1.4 1.6c.8 1.9 2.2 3.3 4.1 4.1l1.6-1.4 3 2.3-1.3 2.3C7.4 13.2 2.8 8.6 1.7 3z" fill="var(--brand-blue)"/>
          </svg>
          480.915.2267
        </li>
        <li class="contact-item">
          <svg class="contact-icon" viewBox="0 0 16 16" aria-hidden="true">
            <rect x="1" y="3.5" width="14" height="9" rx="1" fill="var(--brand-blue)"/>
            <path d="M1.5 4l6.5 5 6.5-5" fill="none" stroke="var(--card)" stroke-width="1.2"/>
          </svg>
          Marcus@rollersandglides-demo.com
        </li>
        <li class="contact-item">
          <svg class="contact-icon" viewBox="0 0 16 16" aria-hidden="true">
            <g fill="none" stroke="var(--brand-blue)" stroke-width="1.3">
              <circle cx="8" cy="8" r="6.5"/>
              <ellipse cx="8" cy="8" rx="3" ry="6.5"/>
              <path d="M1.5 8h13M2.5 4.8h11M2.5 11.2h11"/>
            </g>
          </svg>
          <span>www.<span class="accent">rollersandglides-demo</span>.com</span>
        </li>
      </ul>
    </div>
  </section>

</main>
</body>
</html>
```